Business Card Design

We are a commercial real estate brokerage in San Francisco, leasing office buildings downtown.
I would like a clean, elegant look. Simple but powerful .

Industry/Entity Type

Business

Contact Information for Business Card

Derek Holloway
lic# 07258143
415.555.0172
derek@velt-commercial.example
velt-commercial.example

```html
<!DOCTYPE html>
<html lang="en">
<head>
<meta charset="utf-8">
<title>Velt Commercial – Business Card</title>
<link rel="stylesheet" href="https://fonts.googleapis.com/css2?family=Arimo:wght@400;700&display=swap">
<style>
  :root {
    --page-bg: #d9d6d2;
    --card-bg: #1c1c1e;
    --card-edge: #2a2a2d;
    --brand-blue: #8fa3c6;
    --name-blue: #7f95bd;
    --text-light: #e6e6e6;
    --text-muted: #9a9a9a;
    --divider: #4a4a4e;
  }
  * { box-sizing: border-box; margin: 0; padding: 0; }
  html, body { width: 1200px; height: 787px; overflow: hidden; }
  body {
    background: var(--page-bg);
    font-family: "Arimo", Arial, sans-serif;
    position: relative;
  }
  .card {
    position: absolute;
    width: 560px;
    height: 320px;
    background: var(--card-bg);
    border: 1px solid var(--card-edge);
    box-shadow: 0 10px 28px rgba(0,0,0,.28);
  }
  .card--back { left: 60px; top: 70px; }
  .card--front { left: 580px; top: 397px; }

  /* back side */
  .back-mark {
    position: absolute;
    left: 0; right: 0; top: 92px;
    display: flex; align-items: center; justify-content: center; gap: 14px;
    color: var(--text-muted);
  }
  .back-mark__square { width: 30px; height: 30px; background: var(--text-muted); }
  .back-mark__name { font-size: 34px; letter-spacing: 3px; }
  .tagline {
    position: absolute;
    left: 0; right: 0; top: 178px;
    text-align: center;
    color: var(--text-light);
    font-size: 15px;
    line-height: 22px;
  }

  /* front side */
  .brand {
    position: absolute;
    left: 210px; top: 84px;
    display: flex; align-items: center; gap: 16px;
    padding-left: 18px;
    border-left: 2px solid var(--divider);
  }
  .brand__square { width: 18px; height: 18px; background: var(--brand-blue); }
  .brand__name {
    color: var(--brand-blue);
    font-size: 28px;
    line-height: 30px;
    letter-spacing: 2px;
  }
  .agent {
    position: absolute;
    left: 120px; top: 176px;
    text-align: center;
  }
  .agent__name { color: var(--name-blue); font-size: 19px; }
  .agent__license { color: var(--text-light); font-size: 15px; margin-top: 6px; }
  .contacts {
    position: absolute;
    left: 290px; top: 210px;
    list-style: none;
    color: var(--text-light);
    font-size: 15px;
  }
  .contacts li { display: flex; align-items: center; gap: 8px; height: 22px; }
  .contacts svg { width: 13px; height: 13px; fill: var(--text-light); flex: none; }
</style>
</head>
<body>
  <section class="card card--back" aria-label="Card back">
    <div class="back-mark">
      <span class="back-mark__square"></span>
      <span class="back-mark__name">VELT COMMERCIAL</span>
    </div>
    <p class="tagline">commercial real estate brokerage in San Francisco<br>leasing office buildings downtown.</p>
  </section>

  <section class="card card--front" aria-label="Card front">
    <div class="brand">
      <span class="brand__square"></span>
      <span class="brand__name">VELT<br>COMMERCIAL</span>
    </div>
    <div class="agent">
      <p class="agent__name">Derek Holloway</p>
      <p class="agent__license">lic# 07258143</p>
    </div>
    <ul class="contacts">
      <li>
        <svg viewBox="0 0 16 16" aria-hidden="true"><path d="M3 1h3l1.5 4-2 1.3a9 9 0 0 0 4.2 4.2L11 8.5l4 1.5v3a2 2 0 0 1-2 2A13 13 0 0 1 1 3a2 2 0 0 1 2-2z"/></svg>
        415.555.0172
      </li>
      <li>
        <svg viewBox="0 0 16 16" aria-hidden="true"><path d="M1 3h14v10H1z" fill="none" stroke="#e6e6e6" stroke-width="1.6"/><path d="M1 3l7 6 7-6" fill="none" stroke="#e6e6e6" stroke-width="1.6"/></svg>
        derek@velt-commercial.example
      </li>
      <li>
        <svg viewBox="0 0 16 16" aria-hidden="true"><circle cx="8" cy="8" r="6.5" fill="none" stroke="#e6e6e6" stroke-width="1.6"/><path d="M1.5 8h13M8 1.5c-3 3.5-3 9.5 0 13M8 1.5c3 3.5 3 9.5 0 13" fill="none" stroke="#e6e6e6" stroke-width="1.2"/></svg>
        velt-commercial.example
      </li>
    </ul>
  </section>
</body>
</html>
```